University Student Business Card

Looking for a professional university student business card. Student is studying business with a focus on marketing. Some combination using a monogram and/or full name on the front with full name, university details and contact information on the back. Card should be modern design for a young professional. Prefer use of royal blue, black and white but am open to other uses of colour palette if it reinforces young/trendy style. Initials for a monogram are: KR. Full details will be provided in private consultation with designer(s).

Target Market(s)

Professional business people, marketers, advertisers, consultants

Industry/Entity Type

Business, marketing

Contact Information for Business Card

Monogram or personal logo, full name, university name, program of study, phone number, email address, pathfolio address

Other font styles liked:
• Open to suggestion to fulfill above requirements

Colors
0054AA
0677BA
7BADD7
CADEEF
E8F1F8

Requirements
Must have
• Monogram using letters K and R, and incorporate the business card details listed in the brief (specific details including personal contact info will be shared with successful designer to ensure privacy)
Nice to have
• Personal brand using monogram or personal logo (not a business logo)

```html
<!DOCTYPE html>
<html lang="en">
<head>
<meta charset="utf-8">
<title>KR Student Business Card</title>
<link rel="stylesheet" href="https://fonts.googleapis.com/css2?family=Montserrat:wght@500;600;700&family=Arimo:wght@400&display=swap">
<style>
:root{
  --stage:#2b2b2b;
  --navy-deep:#011530;
  --navy:#02204a;
  --royal:#0054AA;
  --royal-bright:#0660b8;
  --white:#ffffff;
  --rule:#6f8fb8;
}
*{margin:0;padding:0;box-sizing:border-box}
html,body{width:1200px;height:1015px;overflow:hidden;background:var(--stage)}
.canvas{position:relative;width:1200px;height:1015px}
.card{position:absolute;left:250px;width:700px;height:400px;overflow:hidden;box-shadow:0 14px 30px rgba(0,0,0,.55)}
.card--front{top:60px;background:linear-gradient(180deg,var(--navy) 0%,var(--royal) 48%,var(--royal-bright) 55%,var(--navy) 100%)}
.card--back{top:545px;background:linear-gradient(160deg,var(--navy) 0%,var(--navy-deep) 100%)}

.front-content{position:absolute;inset:0;display:flex;flex-direction:column;align-items:center;padding-top:74px;color:var(--white)}
.monogram{font-family:"Montserrat",sans-serif;font-weight:700;font-size:96px;line-height:1;letter-spacing:2px}
.person-name{margin-top:34px;font-family:"Montserrat",sans-serif;font-weight:600;font-size:24px;letter-spacing:1px}
.person-title{margin-top:2px;font-family:"Arimo",sans-serif;font-size:17px;letter-spacing:.5px}
.front-rule{margin-top:16px;width:130px;height:1px;background:var(--rule)}
.profile-link{margin-top:18px;display:flex;align-items:center;gap:10px;font-family:"Arimo",sans-serif;font-size:18px}
.profile-dot{width:26px;height:26px;border-radius:50%;background:var(--white)}

.back-art{position:absolute;inset:0}
.back-monogram{position:absolute;left:490px;top:110px;width:200px;text-align:center;font-family:"Montserrat",sans-serif;font-weight:700;font-size:96px;line-height:1;color:var(--navy-deep);letter-spacing:2px}
.back-info{position:absolute;left:46px;top:118px;color:var(--white);font-family:"Arimo",sans-serif}
.university{font-family:"Montserrat",sans-serif;font-weight:700;font-size:24px;color:var(--royal);letter-spacing:1px;white-space:nowrap}
.address{margin-top:42px;font-size:17px;line-height:1.25}
.back-rule{margin-top:10px;width:140px;height:1px;background:var(--rule);opacity:.6}
.contacts{margin-top:50px;list-style:none;font-size:17px;line-height:1.35}
.contacts li{display:flex;align-items:center;gap:10px}
.contacts svg{width:16px;height:16px;flex:none}
</style>
</head>
<body>
<main class="canvas">
  <section class="card card--front" aria-label="Card front">
    <div class="front-content">
      <div class="monogram">KR</div>
      <div class="person-name">MARCUS HOLLOWAY</div>
      <div class="person-title">Business Marketing</div>
      <div class="front-rule"></div>
      <div class="profile-link"><span class="profile-dot"></span><span>pathfolio.com/name</span></div>
    </div>
  </section>

  <section class="card card--back" aria-label="Card back">
    <svg class="back-art" viewBox="0 0 700 400" aria-hidden="true">
      <circle cx="590" cy="150" r="250" fill="#ffffff"/>
      <path d="M372 70 C 330 200 400 330 590 390" fill="none" stroke="#0054AA" stroke-width="5" stroke-linecap="round"/>
    </svg>
    <div class="back-monogram">KR</div>
    <div class="back-info">
      <div class="university">UNIVERSITY NAME</div>
      <div class="address">88, Harbour Lane West<br>30917, Country Name</div>
      <div class="back-rule"></div>
      <ul class="contacts">
        <li><svg viewBox="0 0 16 16"><path d="M3 1l3 3-1.5 2a9 9 0 0 0 5.5 5.5L12 10l3 3-2 2C7 15 1 9 1 3z" fill="#0054AA"/></svg>044-555 018 274</li>
        <li><svg viewBox="0 0 16 16"><rect x="1" y="3" width="14" height="10" fill="#0054AA"/><path d="M1 3l7 6 7-6" fill="none" stroke="#011530" stroke-width="1.2"/></svg>info@kestrelmail.com</li>
        <li><svg viewBox="0 0 16 16"><g fill="none" stroke="#0054AA" stroke-width="1.3"><circle cx="8" cy="8" r="6.5"/><ellipse cx="8" cy="8" rx="3" ry="6.5"/><path d="M1.5 8h13M2.5 5h11M2.5 11h11"/></g></svg>www.kestrelroad.com</li>
      </ul>
    </div>
  </section>
</main>
</body>
</html>
```